NEW Wordpress Website Design for a Dynamic Long Term Healthcare Company in Hawaii

I would like a new website design for my current company, Marlow Health Collective, which has two different brands - Marlow Homecare and Marlow Senior Living. You can see the current website at www.marlowhealth-example.com. The website should be built using Wordpress Software and the Framewise theme. The website should have a local Hawaii island/tropical feel, but look professional for healthcare. I'm looking for something fresh, and want the designer to select colors, styles, etc.

In the Header, on all pages, I would like a menu that includes Home Care, Senior Living, Rates, and About Us.
Under each of the Header Menu Titles, I would like these drop downs included:
Home Care (drop down pages)- Nurse Aide Care, 24-Hour Home Care, Skilled Nursing, Lifestyle Aide, Hospice at Home, Bathing & Meal Service.
Senior Living (drop down pages) - Long-Term Stay, Short-Term Stay.
Rates (drop down page) - Rates.
About Us (drop down pages) - Our Mission, Ohana Talk, About Dana Marlow.

In the footer, on all pages, you should include the address: 248 Pueo Lane, Suite 310, Honolulu, HI 96817. Phone number: 808-555-0172
The footer should also include buttons for a page called Learn, Caregiver Jobs, and each of the service page links to include: Nurse Aide Care, 24-Hour Home Care, Skilled Nursing, Lifestyle Aide, Hospice at Home, Bathing & Meal Service.
Please don't take the current website and redesign a few aspects. I'm looking for a completely different look and feel.

Target Market(s)

40-80 year olds

Industry/Entity Type

Long Term Healthcare

Coding

Coded - Design and coding required

Requirements
Should not have
• Our existing website as a template. We are looking for a complete redesign. Thank you.

```html
<!DOCTYPE html>
<html lang="en">
<head>
<meta charset="utf-8">
<title>Marlow Health Collective — Homecare &amp; Senior Living</title>
<link href="https://fonts.googleapis.com/css2?family=Cinzel:wght@400;600;700&family=Montserrat:wght@400;500;600;700&display=swap" rel="stylesheet">
<style>
:root{
  --coral:#f4968a;
  --coral-deep:#ef8576;
  --teal:#55b1b7;
  --teal-deep:#3f9ea5;
  --cream:#fbe8dc;
  --ink:#2b2b2b;
  --body:#3d3d3d;
  --white:#ffffff;
  --sand:#c89a6c;
}
*{box-sizing:border-box;margin:0;padding:0}
html,body{width:1200px;height:4386px;overflow:hidden;background:var(--white)}
body{position:relative;font-family:"Montserrat",sans-serif;color:var(--body)}
.abs{position:absolute}
.serif{font-family:"Cinzel",serif}
.pill{position:absolute;display:flex;align-items:center;justify-content:center;gap:6px;border-radius:30px;color:var(--white);font-size:13px;font-weight:600;letter-spacing:.5px;text-transform:uppercase}
.pill.coral{background:var(--coral)}
.pill.teal{background:var(--teal)}
.photo{position:absolute}

/* header */
.site-header{position:absolute;top:0;left:0;width:1200px;height:82px;background:var(--white);z-index:5}
.brand{position:absolute;display:flex;align-items:center;gap:10px;font-weight:600;color:var(--coral)}
.brand .dot{width:30px;height:30px;border-radius:50%;background:var(--coral)}
.site-header .brand{left:115px;top:22px;font-size:22px}
.main-nav{position:absolute;top:33px;left:390px;display:flex;gap:34px;font-size:13px;font-weight:500;color:var(--ink)}
.main-nav span::after{content:"";display:inline-block;width:6px;height:6px;border-right:1.3px solid #999;border-bottom:1.3px solid #999;transform:rotate(45deg);margin-left:7px;position:relative;top:-3px}
.header-phone{position:absolute;left:928px;top:26px;display:flex;align-items:center;gap:10px;font-size:20px;font-weight:700;color:var(--ink)}
.phone-badge{width:30px;height:30px;border-radius:50%;background:var(--coral);display:flex;align-items:center;justify-content:center}

/* hero */
.hero{position:absolute;top:82px;left:0;width:1200px;height:640px;background:linear-gradient(90deg,#fbe3d5 0%,#fdf1ea 45%,#fbe8dc 60%)}
.hero .photo{left:540px;top:0;width:660px;height:620px;background:linear-gradient(90deg,rgba(251,232,220,1) 0%,rgba(196,150,110,.75) 22%,#9c6e4b 55%,#7d9c6a 100%)}
.hero-kicker{left:115px;top:158px;font-size:22px;font-weight:500;color:var(--ink);letter-spacing:.3px}
.hero-title{left:115px;top:190px;font-size:62px;line-height:72px;color:var(--ink);font-weight:400}
.hero-title .accent{color:var(--coral)}

/* mission */
.mission-leaves{left:95px;top:725px;width:530px;height:530px;border-radius:50%;background:radial-gradient(circle,#7dbb5a 55%,rgba(125,187,90,0) 72%)}
.mission-photo{left:140px;top:802px;width:392px;height:392px;border-radius:50%;border:8px solid var(--coral);background:linear-gradient(160deg,#6fa657,#8fb878 50%,#c9c4b6)}
.section-title{font-family:"Cinzel",serif;color:var(--ink);font-weight:400}
.rule{position:absolute;height:3px;background:var(--teal);width:80px}
.rule.short::after{content:"";position:absolute;left:14px;top:7px;width:52px;height:2px;background:var(--teal)}
.mission-title{left:635px;top:818px;font-size:48px}
.mission-text{left:637px;top:912px;width:520px;font-size:16.5px;line-height:29px;color:var(--body)}

/* home care */
.homecare{position:absolute;top:1290px;left:0;width:1200px;height:752px;overflow:hidden}
.homecare-bg{position:absolute;left:0;top:40px;width:1200px;height:712px;background:linear-gradient(180deg,#52aeb4,#4aa7ae 60%,#5ab3b8)}
.homecare h2{position:absolute;top:140px;width:1200px;text-align:center;font-family:"Cinzel",serif;font-weight:400;font-size:44px;color:var(--white)}
.homecare .lede{position:absolute;top:218px;left:210px;width:780px;text-align:center;font-size:18.5px;line-height:24px;color:var(--white)}
.homecare .photo{left:341px;top:472px;width:560px;height:560px;border-radius:50%;background:linear-gradient(160deg,#d9cf6a,#b9a86b 45%,#8f6a4e)}
.svc{position:absolute;width:76px;height:76px;border-radius:50%;background:var(--coral);border:3px solid #ffd2c9;display:flex;align-items:center;justify-content:center}
.svc::after{content:"";width:34px;height:34px;border-radius:50%;border:2.5px solid var(--white)}
.svc-label{position:absolute;font-size:17px;font-weight:700;line-height:18px;color:var(--white);text-transform:uppercase}
.svc-label.left{text-align:right}

/* senior living */
.senior{position:absolute;top:2042px;left:0;width:1200px;height:651px;background:linear-gradient(90deg,#fdf0e8,#fbe8dc 55%)}
.senior .photo{left:560px;top:0;width:640px;height:651px;background:linear-gradient(90deg,rgba(251,232,220,1) 0%,rgba(214,190,150,.8) 20%,#c9b188 45%,#9a6c48 100%)}
.senior-title{left:124px;top:120px;font-size:50px}
.senior-text{left:124px;top:220px;width:460px;font-size:16.5px;line-height:27px}
.senior-list{left:124px;top:374px;list-style:none;font-size:17px;font-weight:600;color:var(--ink)}
.senior-list li{height:35px;display:flex;gap:10px;align-items:center;text-transform:uppercase}

/* testimonials */
.testi-title{left:0;top:2756px;width:1200px;text-align:center;font-family:"Cinzel",serif;font-weight:700;font-size:40px;color:var(--ink)}
.card{position:absolute;top:2864px;width:446px;height:260px;border:2px solid var(--teal);border-radius:26px 4px 26px 4px;background:var(--white);padding:30px 50px 0 50px}
.card p{font-size:15.5px;line-height:27px;color:var(--body)}
.card .who{margin-top:14px;font-size:15px;font-weight:700;color:var(--ink)}
.card .stars{font-size:22px;color:#f0a23b;letter-spacing:2px}
.card .quote{position:absolute;right:34px;bottom:28px;font-family:"Cinzel",serif;font-size:90px;line-height:40px;color:#f08f4a;font-weight:700}

/* consultation */
.consult-band{left:0;top:3251px;width:1200px;height:664px}
.consult-photo{left:618px;top:3290px;width:600px;height:610px;border-radius:50% 50% 46% 54%;background:linear-gradient(150deg,#e8df8c,#b3a070 50%,#7a5e4d)}
.consult-title{left:108px;top:3362px;font-family:"Cinzel",serif;font-size:41px;line-height:42px;color:var(--white);font-weight:400}
.field{position:absolute;background:var(--white);border:1px solid #e7c0b8;font-size:13px;color:#555;padding:12px 18px}

/* footer */
.foot-col{position:absolute;top:3982px}
.foot-col h3{font-size:20px;font-weight:500;color:var(--ink);padding-left:14px;border-left:3px solid var(--coral);line-height:20px;margin-bottom:16px}
.foot-col li{list-style:none;font-size:14px;line-height:30px;color:var(--ink);padding-left:18px}
.social{position:absolute;top:4180px;width:30px;height:30px;border-radius:50%}
.contact-row{position:absolute;display:flex;gap:12px;font-size:14.5px;line-height:18px;color:var(--ink)}
.icon-circle{width:32px;height:32px;border-radius:50%;background:var(--teal);flex:none;display:flex;align-items:center;justify-content:center}
.footer-brand{position:absolute;top:4160px;font-size:25px;font-weight:600;line-height:28px;text-align:center}
.copyright{left:0;top:4308px;width:1200px;text-align:center;font-size:12px;color:var(--ink)}
</style>
</head>
<body>

<header class="site-header">
  <div class="brand"><span class="dot"></span>Marlow</div>
  <nav class="main-nav"><span>HOME CARE</span><span>SENIOR LIVING</span><span>RATES</span><span>ABOUT US</span></nav>
  <div class="header-phone">
    <span class="phone-badge"><svg width="15" height="15" viewBox="0 0 24 24"><path fill="#fff" d="M6.6 10.8a15.1 15.1 0 0 0 6.6 6.6l2.2-2.2c.3-.3.7-.4 1-.2 1.1.4 2.3.6 3.6.6.6 0 1 .4 1 1V20c0 .6-.4 1-1 1A17 17 0 0 1 3 4c0-.6.4-1 1-1h3.5c.6 0 1 .4 1 1 0 1.2.2 2.4.6 3.6.1.3 0 .7-.2 1z"/></svg></span>
    808-555-0172
  </div>
</header>

<section class="hero">
  <div class="photo" role="img" aria-label="Caregiver in blue scrubs chatting with a smiling senior woman on a leather sofa in a bright lanai living room"></div>
  <svg class="abs" style="left:0;top:560px" width="1200" height="80" viewBox="0 0 1200 80"><path fill="#fff" d="M0 40 C200 10 380 70 600 45 C820 20 1000 60 1200 30 L1200 80 L0 80 Z"/></svg>
  <div class="abs hero-kicker">MARLOW HEALTH COLLECTIVE</div>
  <h1 class="abs serif hero-title"><span class="accent">Homecare &amp;</span><br>Senior Living</h1>
  <div class="pill coral" style="left:119px;top:358px;width:174px;height:46px">View Rates ›</div>
  <div class="pill teal" style="left:310px;top:358px;width:174px;height:46px">Contact Us ›</div>
</section>

<section class="mission">
  <div class="abs mission-leaves" role="img" aria-label="Ring of tropical palm fronds with a plumeria flower"></div>
  <div class="photo mission-photo" role="img" aria-label="Caregiver helping a woman with a walker along a tropical garden path"></div>
  <h2 class="abs section-title mission-title">Our Mission</h2>
  <div class="rule short" style="left:640px;top:884px"></div>
  <p class="abs mission-text">At Marlow Health Collective, our mission is to provide compassionate and professional long-term healthcare services that empower individuals to maintain their highest level of independence, health, and well-being in the comfort of their own homes or ours, either through our licensed home healthcare agency</p>
  <div class="pill coral" style="left:632px;top:1114px;width:186px;height:46px">Learn More ›</div>
</section>

<section class="homecare">
  <svg class="abs" style="left:0;top:0" width="1200" height="90" viewBox="0 0 1200 90"><path fill="#52aeb4" d="M0 30 C150 60 300 75 480 55 C650 35 760 15 900 25 C1030 35 1120 30 1200 20 L1200 90 L0 90 Z"/></svg>
  <div class="homecare-bg"></div>
  <h2>Home Care</h2>
  <div class="rule" style="left:570px;top:198px;height:2px;width:60px;background:#fff"></div>
  <p class="lede">Marlow Homecare understands that every person's care journey is unique. We tailor our in-home services to meet the diverse nurturing experience</p>
  <svg class="abs" style="left:0;top:0" width="1200" height="752"><circle cx="621" cy="752" r="336" fill="none" stroke="#fff" stroke-width="3"/></svg>
  <div class="photo" role="img" aria-label="Caregiver assisting a senior man seated on his bed in a sunny bedroom"></div>

  <div class="svc" style="left:413px;top:335px"></div>
  <div class="svc-label left" style="left:290px;top:345px;width:112px">Skilled<br>Nursing</div>
  <div class="svc" style="left:738px;top:326px"></div>
  <div class="svc-label" style="left:825px;top:345px">Lifestyle<br>Aide</div>
  <div class="svc" style="left:296px;top:442px"></div>
  <div class="svc-label left" style="left:130px;top:462px;width:152px">24-Hour<br>Home Care</div>
  <div class="svc" style="left:864px;top:456px"></div>
  <div class="svc-label" style="left:950px;top:472px">Hospice<br>at Home</div>
  <div class="svc" style="left:248px;top:595px"></div>
  <div class="svc-label left" style="left:110px;top:615px;width:128px">Nurse<br>Aide Care</div>
  <div class="svc" style="left:912px;top:595px"></div>
  <div class="svc-label" style="left:997px;top:612px">Bathing &amp;<br>Meal Service</div>
</section>

<section class="senior">
  <div class="photo" role="img" aria-label="Three women knitting together on a sofa in a warm senior living lounge"></div>
  <h2 class="abs section-title senior-title">Senior Living</h2>
  <div class="rule short" style="left:128px;top:190px"></div>
  <p class="abs senior-text">Marlow Senior Living creates a warm, supportive, and enriching care home environment where seniors can thrive in their golden years. We provide residential care that promotes well-being, connection, and dignity of each individual.</p>
  <ul class="abs senior-list">
    <li><svg width="10" height="14" viewBox="0 0 10 14"><path d="M2 2l5 5-5 5" stroke="#55b1b7" stroke-width="2.5" fill="none"/></svg>Long-Term Stay</li>
    <li><svg width="10" height="14" viewBox="0 0 10 14"><path d="M2 2l5 5-5 5" stroke="#55b1b7" stroke-width="2.5" fill="none"/></svg>Short-Term Stay</li>
  </ul>
  <div class="pill teal" style="left:119px;top:457px;width:186px;height:50px">Learn More ›</div>
</section>

<h2 class="abs testi-title">Testimonials</h2>
<div class="rule" style="left:576px;top:2817px;width:48px;height:2px"></div>
<div class="rule" style="left:586px;top:2824px;width:28px;height:2px"></div>

<article class="card" style="left:153px">
  <p>"Lorem ipsum dolor sit amet, consectetur adipiscing elit, sed do eiusmod tempor incididunt ut labore et dolore magna aliqua. Quis ipsum suspendisse ultrices gravida. Risus commodo viverra maecenas"</p>
  <div class="who">Keoni Alana</div>
  <div class="stars">★★★★★</div>
  <div class="quote">”</div>
</article>
<article class="card" style="left:626px">
  <p>"Lorem ipsum dolor sit amet, consectetur adipiscing elit, sed do eiusmod tempor incididunt ut labore et dolore magna aliqua. Quis ipsum suspendisse ultrices gravida. Risus commodo viverra maecenas"</p>
  <div class="who">Keoni Alana</div>
  <div class="stars">★★★★★</div>
  <div class="quote">”</div>
</article>

<svg class="abs consult-band" width="1200" height="664" viewBox="0 0 1200 664"><path fill="#f69a8c" d="M0 0 L1200 0 L1200 620 C1050 610 950 650 800 630 C600 600 300 640 0 610 Z"/></svg>
<div class="photo consult-photo" role="img" aria-label="Senior residents exercising with hand weights alongside a smiling instructor"></div>
<h2 class="abs consult-title">Schedule a Care<br>Consultation</h2>
<div class="rule" style="left:110px;top:3455px;width:72px;height:3px;background:#fff"></div>
<div class="field" style="left:111px;top:3494px;width:238px;height:46px">First Name</div>
<div class="field" style="left:357px;top:3494px;width:238px;height:46px">Last Name</div>
<div class="field" style="left:111px;top:3549px;width:238px;height:45px">Email address</div>
<div class="field" style="left:357px;top:3549px;width:238px;height:45px">Phone Number</div>
<div class="field" style="left:111px;top:3603px;width:484px;height:100px">Message</div>
<div class="pill teal" style="left:111px;top:3718px;width:198px;height:46px">Send Message ›</div>

<footer>
  <div class="brand" style="left:120px;top:4000px;font-size:34px"><span class="dot" style="width:40px;height:40px"></span>Marlow</div>
  <div class="pill teal" style="left:130px;top:4070px;width:181px;height:36px;border-radius:2px;font-size:11px">Learn</div>
  <div class="pill coral" style="left:130px;top:4120px;width:181px;height:36px;border-radius:2px;font-size:11px">Caregiver Jobs</div>
  <div class="social" style="left:153px;background:var(--coral)" aria-label="Social link"></div>
  <div class="social" style="left:192px;background:var(--teal)" aria-label="Social link"></div>
  <div class="social" style="left:230px;background:var(--teal)" aria-label="Social link"></div>
  <div class="social" style="left:268px;background:var(--teal)" aria-label="Social link"></div>

  <div class="foot-col" style="left:380px"><h3>Navigation</h3><ul><li>Home Care</li><li>Senior Living</li><li>Rates</li><li>About Us</li></ul></div>
  <div class="foot-col" style="left:586px"><h3>Services</h3><ul><li>Nurse Aide Care</li><li>24-Hour Home Care</li><li>Skilled Nursing</li><li>Lifestyle Aide</li><li>Hospice at Home</li><li>Bathing &amp; Meal Service</li></ul></div>
  <div class="foot-col" style="left:816px"><h3>Contact Us</h3></div>
  <div class="contact-row" style="left:832px;top:4030px">
    <span class="icon-circle"><svg width="14" height="16" viewBox="0 0 24 28"><path fill="#fff" d="M12 0a10 10 0 0 0-10 10c0 7.5 10 18 10 18s10-10.5 10-18A10 10 0 0 0 12 0zm0 14a4 4 0 1 1 0-8 4 4 0 0 1 0 8z"/></svg></span>
    <span>248 Pueo Lane, Suite 310,<br>Honolulu, HI 96817</span>
  </div>
  <div class="contact-row" style="left:832px;top:4080px">
    <span class="icon-circle"><svg width="14" height="14" viewBox="0 0 24 24"><path fill="#fff" d="M6.6 10.8a15.1 15.1 0 0 0 6.6 6.6l2.2-2.2c.3-.3.7-.4 1-.2 1.1.4 2.3.6 3.6.6.6 0 1 .4 1 1V20c0 .6-.4 1-1 1A17 17 0 0 1 3 4c0-.6.4-1 1-1h3.5c.6 0 1 .4 1 1 0 1.2.2 2.4.6 3.6.1.3 0 .7-.2 1z"/></svg></span>
    <span>Phone number<br><b style="font-size:16px">808-555-0172</b></span>
  </div>
  <div class="footer-brand" style="left:826px;width:120px;color:var(--coral)">Marlow<br><span style="font-size:12px;letter-spacing:2px">HOMECARE</span></div>
  <div class="footer-brand" style="left:955px;width:140px;color:var(--teal);font-size:22px">Marlow<br><span style="font-size:12px;letter-spacing:1px">SENIOR LIVING</span></div>

  <div class="abs" style="left:0;top:4282px;width:1200px;height:1px;background:#e3e3e3"></div>
  <p class="abs copyright">Copyright © 2024 <u>Marlow Health Collective</u>. All Right Reserved</p>
</footer>

</body>
</html>
```